Summer Sunglass offer

Need a poster design for a spring / summer campaign. We are an opticians with good footfall. The design needs to be eye catching and aimed at 40 year old plus. The offer is Up to 50% off sunglass offer, t&c apply. (I have attached our last year campaign)
Also need a 2 sided A5 leaflet design (see attached)
I've uploaded a copy of our logo

A5 leaflet should read:

Grab a bargain on two great looks this summer Upto 50% off sunglasses
Look great and stay safe in the sun this summer

We want you to look great, feel fantastic and most of all stay safe in the sun this summer. That’s why we’re offering you 50% off prescription sunglasses with every complete pair of glasses you buy this summer or 25% off for prescription sunglasses with no other purchase.
Find you new summer looks from our gorgeous collection of frames in store. It matters to us that you look great in your new glasses as much as how well you see through them, so we’ll be on hand to help you find frames that suit you best.
What new looks will you go for? Smart or sassy? Formal or Fun? Whatever you’re in the mood for, you’ll find it in our collections this summer.
Call in today to find your new looks, and remember to bring your prescription if you don’t need an eye test.

Target Market(s)

40 + year old

Industry/Entity Type

Optician

Colors

Designer to choose colors to be used in the design.

Requirements
Must have
• Images, preferably a male and Female image

```html
<!DOCTYPE html>
<html lang="en">
<head>
<meta charset="utf-8">
<title>Summer Sunglasses Offer – Brightwell Eyecare Centre</title>
<link rel="stylesheet" href="https://fonts.googleapis.com/css2?family=Lato:wght@400;700&display=swap">
<style>
  :root {
    --teal: #43a4a7;
    --teal-band: #4aa9ab;
    --offer-red: #e30a3c;
    --paper: #ffffff;
    --body-text: #ffffff;
  }
  html, body {
    margin: 0;
    padding: 0;
    overflow: hidden;
    background: var(--paper);
  }
  .leaflet {
    position: relative;
    width: 851px;
    height: 1200px;
    overflow: hidden;
    background: var(--paper);
    font-family: "Lato", "Gill Sans", sans-serif;
  }
  .headline {
    position: absolute;
    top: 6px;
    left: 0;
    width: 100%;
    margin: 0;
    text-align: center;
    color: var(--teal);
    font-size: 24px;
    font-weight: 400;
    line-height: 26px;
    letter-spacing: 0.4px;
    text-transform: uppercase;
  }
  .headline strong { font-weight: 700; }
  .band {
    position: absolute;
    left: 0;
    width: 100%;
    height: 12px;
    background: var(--teal-band);
  }
  .band--top { top: 136px; }
  .band--bottom { top: 1040px; }
  .offer-panel {
    position: absolute;
    top: 148px;
    left: 0;
    width: 100%;
    height: 892px;
    background: var(--offer-red);
    color: var(--body-text);
    text-align: center;
    box-sizing: border-box;
    padding-top: 18px;
  }
  .offer-panel p {
    margin: 0 0 33px;
    font-size: 24px;
    line-height: 32.6px;
  }
  .offer-panel strong { font-weight: 700; }
  .brand {
    position: absolute;
    top: 1080px;
    left: 0;
    width: 100%;
    display: flex;
    align-items: center;
    justify-content: center;
    gap: 14px;
    color: var(--teal);
  }
  .brand__dot {
    width: 44px;
    height: 44px;
  }
  .brand__name {
    font-size: 30px;
    font-weight: 400;
    letter-spacing: 2px;
    text-transform: uppercase;
  }
  .web-address {
    position: absolute;
    top: 1160px;
    left: 0;
    width: 100%;
    text-align: center;
    color: var(--teal);
    font-size: 21px;
    letter-spacing: 0.3px;
  }
</style>
</head>
<body>
<main class="leaflet">
  <h1 class="headline">
    Grab a bargain on two great looks this summer<br>
    <strong>Upto 50% off sunglasses.</strong><br>
    Look great and stay safe in the sun this summer.
  </h1>

  <div class="band band--top"></div>

  <section class="offer-panel">
    <p>We want you to look great, feel fantastic and<br>
    most of all stay safe in the sun this summer.<br>
    That’s why we’re offering you <strong>50</strong>% off prescription<br>
    sunglasses with every complete pair of glasses<br>
    you buy this summer<br>
    or <strong>25</strong>% off for prescription sunglasses<br>
    with no other purchase.</p>

    <p>Find you new summer looks from our gorgeous<br>
    collection of frames in store.<br>
    It matters to us that you love how you look<br>
    in your new glasses as much as how well<br>
    you see through them,<br>
    so we’ll be on hand to help you find frames<br>
    that suit you best.<br>
    What new looks will you go for? Smart or sassy?<br>
    Formal or Fun? Whatever you’re in the mood for,<br>
    you’ll find it in our collections this summer.</p>

    <p>Call in today to find your new looks, and remember<br>
    to bring your prescription if you don’t need an eye test.</p>
  </section>

  <div class="band band--bottom"></div>

  <div class="brand">
    <svg class="brand__dot" viewBox="0 0 44 44" aria-hidden="true">
      <circle cx="22" cy="22" r="19" fill="none" stroke="#43a4a7" stroke-width="5"/>
    </svg>
    <span class="brand__name">Brightwell Eyecare Centre</span>
  </div>

  <div class="web-address">brightwelleyecare.co.uk</div>
</main>
</body>
</html>
```